Larkspur Cosmetics Website needs a professional upgrade

I need a new design for an online cosmetics store that looks professional and clean but also has a natural look and feel to it.

The women in the top bar (Image attached) needs to be included and she is on all of our advertising banners/ stands though I would like to come away from the black.

Design Needs:
- 1 x Home Page
- 1 x Products Page

I have plenty more website coming along so hopefully can find someone who I can rely on for a quick turnover :)

Happy designing !

Industry/Entity Type

Store

Number of Pages Required

2 page

Font styles to use
Sans Serif

Requirements
Must have
• - Natural Clean look
Should not have
• - The current black and green colours

```html
<!DOCTYPE html>
<html lang="en">
<head>
<meta charset="utf-8">
<title>Larkspur Cosmetics – Home</title>
<link rel="stylesheet" href="https://fonts.googleapis.com/css2?family=Montserrat:wght@300;400;500&family=Open+Sans:wght@400;600&display=swap">
<style>
:root{
  --orange:#f08a46;
  --orange-soft:#f5a26c;
  --orange-band:#ef8a4a;
  --price:#e6403f;
  --ink:#2e2e2e;
  --muted:#6b6b6b;
  --line:#dcdcdc;
  --card-band:#f2f2f2;
  --white:#ffffff;
}
*{box-sizing:border-box;margin:0;padding:0}
html,body{width:1200px;height:2222px;overflow:hidden;background:var(--white)}
body{position:relative;font-family:"Open Sans",Arial,sans-serif;color:var(--ink)}
.abs{position:absolute}
.top-rule{left:0;top:0;width:1200px;height:5px;background:var(--orange)}

/* header */
.phone{left:92px;top:44px;display:flex;align-items:center;gap:12px;font-family:"Montserrat",sans-serif;font-size:18px;letter-spacing:.5px;color:var(--ink)}
.phone-icon{width:18px;height:18px;border-radius:3px;background:var(--orange);display:flex;align-items:center;justify-content:center}
.brand{left:500px;top:16px;width:200px;text-align:center;font-family:"Montserrat",sans-serif}
.brand-dot{width:52px;height:52px;border-radius:50%;background:#3a3326;margin:0 auto 8px}
.brand-name{font-size:17px;font-weight:400;letter-spacing:1px;color:var(--ink)}
.account{right:90px;top:44px;font-family:"Montserrat",sans-serif;font-size:12px;color:#555;letter-spacing:.4px}
.account .cart-count{color:var(--orange)}
.nav{left:90px;top:122px;width:1020px;display:flex;justify-content:space-between;align-items:center;font-family:"Montserrat",sans-serif;font-size:13px;letter-spacing:.6px;color:#333}
.nav a{color:inherit;text-decoration:none}
.nav .active{color:var(--orange);border:1.5px solid var(--orange);border-radius:16px;padding:6px 20px}

/* hero */
.hero{left:0;top:175px;width:1200px;height:505px;background:linear-gradient(90deg,#f7f7f7 0%,#efefef 45%,#e9edf3 100%);border-top:1px solid #e5e5e5;border-bottom:1px solid #e5e5e5}
.hero-products{left:532px;top:300px;width:260px;height:330px;background:linear-gradient(180deg,#e8e4da 0%,#c9bd97 55%,#e9e9e9 100%);border-radius:6px}
.hero-model{left:810px;top:176px;width:390px;height:503px;background:radial-gradient(ellipse at 55% 45%,#e9c9b3 0%,#d8b39a 40%,#dfe6ef 80%)}
.hero-title{left:90px;top:362px;font-family:"Montserrat",sans-serif;font-weight:400;font-size:30px;letter-spacing:.5px;color:var(--orange)}
.hero-sub{left:90px;top:404px;font-family:"Montserrat",sans-serif;font-weight:400;color:#333;line-height:1.22}
.hero-sub .l1{font-size:26px}
.hero-sub .l2{font-size:22px}
.btn-buy{left:90px;top:481px;width:126px;height:38px;border:1.5px solid var(--orange);border-radius:19px;color:var(--orange);font-family:"Montserrat",sans-serif;font-size:15px;display:flex;align-items:center;justify-content:center;background:#fff;box-shadow:0 2px 4px rgba(0,0,0,.08)}
.hero-arrows{left:90px;top:562px;display:flex;gap:4px}
.round-arrow{width:27px;height:27px;border-radius:50%;background:#777;display:flex;align-items:center;justify-content:center}

/* products */
.section-title{left:86px;top:770px;font-family:"Montserrat",sans-serif;font-size:22px;letter-spacing:.5px;color:#222}
.section-title span{color:var(--orange)}
.section-arrows{left:1084px;top:766px;display:flex;gap:8px}
.section-rule{left:86px;top:815px;width:1029px;height:2px;background:var(--line)}
.card{width:243px;height:336px;background:#fff;box-shadow:0 1px 5px rgba(0,0,0,.18)}
.card-photo{position:absolute;left:8px;top:8px;width:227px;height:195px;background:radial-gradient(ellipse at 50% 55%,#d9cfae 0%,#ece8dc 45%,#f8f8f8 80%)}
.card-photo.green{background:radial-gradient(ellipse at 50% 55%,#b9cf78 0%,#e3ead0 45%,#f8f8f8 80%)}
.card-name{position:absolute;left:0;top:205px;width:100%;height:36px;background:var(--card-band);display:flex;align-items:center;justify-content:center;font-size:14px;color:#444}
.card-price{position:absolute;left:0;top:245px;width:100%;height:44px;display:flex;align-items:center;justify-content:center;gap:10px}
.old{font-size:13px;color:#999;text-decoration:line-through}
.now{font-size:18px;color:var(--price)}
.card-actions{position:absolute;left:0;bottom:0;width:100%;height:45px;display:flex;border-top:1px solid #e4e4e4}
.card-actions div{flex:1;display:flex;align-items:center;justify-content:center;border-left:1px solid #e4e4e4}
.card-actions div:first-child{border-left:none;background:var(--orange-soft)}

/* news */
.news{left:0;top:1619px;width:1200px;height:304px;background:linear-gradient(90deg,#e9834a 0%,#f09458 50%,#ec8a4e 100%)}
.news-title{left:0;top:1664px;width:1200px;text-align:center;font-family:"Montserrat",sans-serif;font-size:26px;color:#fff;letter-spacing:.5px}
.news-photo{width:160px;height:142px;border:3px solid #fff}
.news-photo.a{background:linear-gradient(160deg,#7f9a4e 0%,#c7a27b 55%,#5c6b3c 100%)}
.news-photo.b{background:linear-gradient(180deg,#9d8cd8 0%,#6e6a95 40%,#2f3a26 100%)}
.news-text{width:300px;color:#fff;font-size:11.2px;line-height:19px}
.news-text h3{font-size:14px;font-weight:600;margin-bottom:3px}
.news-text .date{font-weight:600;font-size:12px}
.news-text .more{font-weight:600;margin-top:4px}

/* footer */
.foot-h{top:1988px;font-family:"Montserrat",sans-serif;font-size:15px;color:#333;letter-spacing:.3px}
.foot-body{font-size:11.5px;color:#555;line-height:22px}
.foot-nav{list-style:none;font-size:11.5px;color:#555;line-height:21px}
.foot-nav li::before{content:"▸ ";font-size:9px}
.mail-form{left:631px;top:2066px;display:flex}
.mail-form .field{width:147px;height:30px;border:1px solid #ccc;font-size:11.5px;color:#777;padding:7px 6px}
.mail-form .submit{width:56px;height:30px;background:var(--orange);color:#fff;font-size:12px;display:flex;align-items:center;justify-content:center}
.social{left:936px;top:2036px;display:flex;gap:14px}
.social div{width:24px;height:24px;border-radius:4px;background:#555}
.foot-rule{left:90px;top:2156px;width:1021px;height:1px;background:#ccc}
.pay{left:94px;top:2176px;display:flex;gap:6px}
.pay div{width:40px;height:25px;border-radius:3px}
.copyright{right:89px;top:2177px;font-size:12px;color:#333}
</style>
</head>
<body>
<div class="abs top-rule"></div>

<header>
  <div class="abs phone">
    <span class="phone-icon"><svg width="11" height="11" viewBox="0 0 24 24"><path fill="#fff" d="M6.6 10.8a15 15 0 0 0 6.6 6.6l2.2-2.2c.3-.3.7-.4 1-.2 1.1.4 2.3.6 3.6.6.6 0 1 .4 1 1V20c0 .6-.4 1-1 1A17 17 0 0 1 3 4c0-.6.4-1 1-1h3.5c.6 0 1 .4 1 1 0 1.3.2 2.5.6 3.6.1.3 0 .7-.2 1z"/></svg></span>
    02 9000 4120
  </div>
  <div class="abs brand">
    <div class="brand-dot"></div>
    <div class="brand-name">LARKSPUR</div>
  </div>
  <div class="abs account">MY ACCOUNT &nbsp;|&nbsp; SHOPPING CART <span class="cart-count">&#128722; : 0</span></div>
  <nav class="abs nav">
    <a class="active">HOME</a><a>ABOUT US</a><a>PRODUCTS</a><a>ABOUT ALOE</a><a>TREATMENTS</a><a>MEDIA</a><a>SUCCESS STORIES</a><a>STOCKISTS</a><a>CONTACT US</a>
  </nav>
</header>

<section>
  <div class="abs hero"></div>
  <div class="abs hero-products" role="img" aria-label="Group of skincare jars, tubes and boxes in gold packaging"></div>
  <div class="abs hero-model" role="img" aria-label="Brand ambassador touching her cheek, beauty portrait"></div>
  <h1 class="abs hero-title">LARKSPUR COSMETICS</h1>
  <p class="abs hero-sub"><span class="l1">Australia produces a range of</span><br><span class="l2">premium natural skincare products</span></p>
  <div class="abs btn-buy">Buy now &raquo;</div>
  <div class="abs hero-arrows">
    <span class="round-arrow"><svg width="10" height="10" viewBox="0 0 10 10"><path d="M6.5 1.5 3 5l3.5 3.5" stroke="#fff" stroke-width="1.8" fill="none"/></svg></span>
    <span class="round-arrow"><svg width="10" height="10" viewBox="0 0 10 10"><path d="M3.5 1.5 7 5 3.5 8.5" stroke="#fff" stroke-width="1.8" fill="none"/></svg></span>
  </div>
</section>

<section>
  <h2 class="abs section-title">OUR <span>PRODUCTS</span></h2>
  <div class="abs section-arrows">
    <svg width="12" height="18" viewBox="0 0 12 18"><path d="M9 2 3 9l6 7" stroke="#222" stroke-width="2" fill="none"/></svg>
    <svg width="12" height="18" viewBox="0 0 12 18"><path d="M3 2l6 7-6 7" stroke="#222" stroke-width="2" fill="none"/></svg>
  </div>
  <div class="abs section-rule"></div>

  <svg width="0" height="0" style="position:absolute">
    <defs>
      <symbol id="i-cart" viewBox="0 0 24 24"><path fill="#fff" d="M7 18a2 2 0 1 0 0 4 2 2 0 0 0 0-4zm10 0a2 2 0 1 0 0 4 2 2 0 0 0 0-4zM5.2 4H2V2h4.6l1 2H21l-3.4 8H8.4l-1 2H19v2H4l2.2-4.3z"/></symbol>
      <symbol id="i-heart" viewBox="0 0 24 24"><path fill="#bbb" d="M12 21 10.6 19.7C5.4 15 2 12 2 8.3 2 5.3 4.4 3 7.4 3c1.7 0 3.4.8 4.6 2.1A6.2 6.2 0 0 1 16.6 3C19.6 3 22 5.3 22 8.3c0 3.7-3.4 6.7-8.6 11.4z"/></symbol>
      <symbol id="i-swap" viewBox="0 0 24 24"><path fill="#aaa" d="M16 3l5 4-5 4V8H4V6h12zM8 13v3h12v2H8v3l-5-4z"/></symbol>
      <symbol id="i-go" viewBox="0 0 24 24"><circle cx="12" cy="12" r="9" fill="none" stroke="#999" stroke-width="2"/><path d="M10.5 8 14.5 12l-4 4" stroke="#999" stroke-width="2" fill="none"/></symbol>
    </defs>
  </svg>

  <!-- row 1 -->
  <article class="abs card" style="left:89px;top:849px">
    <div class="card-photo" role="img" aria-label="Black-lidded cream jar on gold box"></div>
    <div class="card-name">Product Name</div>
    <div class="card-price"><span class="old">$659.00</span><span class="now">$599.99</span></div>
    <div class="card-actions"><div><svg width="18" height="18"><use href="#i-cart"/></svg></div><div><svg width="16" height="16"><use href="#i-heart"/></svg></div><div><svg width="16" height="16"><use href="#i-swap"/></svg></div><div><svg width="16" height="16"><use href="#i-go"/></svg></div></div>
  </article>
  <article class="abs card" style="left:348px;top:849px">
    <div class="card-photo" role="img" aria-label="Serum pump bottle beside its box"></div>
    <div class="card-name">Product Name</div>
    <div class="card-price"><span class="old">$659.00</span><span class="now">$599.99</span></div>
    <div class="card-actions"><div><svg width="18" height="18"><use href="#i-cart"/></svg></div><div><svg width="16" height="16"><use href="#i-heart"/></svg></div><div><svg width="16" height="16"><use href="#i-swap"/></svg></div><div><svg width="16" height="16"><use href="#i-go"/></svg></div></div>
  </article>
  <article class="abs card" style="left:607px;top:849px">
    <div class="card-photo" role="img" aria-label="Cream tube beside gold box"></div>
    <div class="card-name">Product Name</div>
    <div class="card-price"><span class="old">$659.00</span><span class="now">$599.99</span></div>
    <div class="card-actions"><div><svg width="18" height="18"><use href="#i-cart"/></svg></div><div><svg width="16" height="16"><use href="#i-heart"/></svg></div><div><svg width="16" height="16"><use href="#i-swap"/></svg></div><div><svg width="16" height="16"><use href="#i-go"/></svg></div></div>
  </article>
  <article class="abs card" style="left:867px;top:849px">
    <div class="card-photo" role="img" aria-label="Stack of lip balm pots"></div>
    <div class="card-name">Product Name</div>
    <div class="card-price"><span class="old">$659.00</span><span class="now">$599.99</span></div>
    <div class="card-actions"><div><svg width="18" height="18"><use href="#i-cart"/></svg></div><div><svg width="16" height="16"><use href="#i-heart"/></svg></div><div><svg width="16" height="16"><use href="#i-swap"/></svg></div><div><svg width="16" height="16"><use href="#i-go"/></svg></div></div>
  </article>

  <!-- row 2 -->
  <article class="abs card" style="left:89px;top:1215px">
    <div class="card-photo green" role="img" aria-label="Gel tube beside green box"></div>
    <div class="card-name">Product Name</div>
    <div class="card-price"><span class="old">$659.00</span><span class="now">$599.99</span></div>
    <div class="card-actions"><div><svg width="18" height="18"><use href="#i-cart"/></svg></div><div><svg width="16" height="16"><use href="#i-heart"/></svg></div><div><svg width="16" height="16"><use href="#i-swap"/></svg></div><div><svg width="16" height="16"><use href="#i-go"/></svg></div></div>
  </article>
  <article class="abs card" style="left:348px;top:1215px">
    <div class="card-photo green" role="img" aria-label="Soap bar in open green gift box"></div>
    <div class="card-name">Product Name</div>
    <div class="card-price"><span class="old">$659.00</span><span class="now">$599.99</span></div>
    <div class="card-actions"><div><svg width="18" height="18"><use href="#i-cart"/></svg></div><div><svg width="16" height="16"><use href="#i-heart"/></svg></div><div><svg width="16" height="16"><use href="#i-swap"/></svg></div><div><svg width="16" height="16"><use href="#i-go"/></svg></div></div>
  </article>
  <article class="abs card" style="left:607px;top:1215px">
    <div class="card-photo green" role="img" aria-label="Green bottle of aloe juice"></div>
    <div class="card-name">Product Name</div>
    <div class="card-price"><span class="old">$659.00</span><span class="now">$599.99</span></div>
    <div class="card-actions"><div><svg width="18" height="18"><use href="#i-cart"/></svg></div><div><svg width="16" height="16"><use href="#i-heart"/></svg></div><div><svg width="16" height="16"><use href="#i-swap"/></svg></div><div><svg width="16" height="16"><use href="#i-go"/></svg></div></div>
  </article>
  <article class="abs card" style="left:867px;top:1215px">
    <div class="card-photo green" role="img" aria-label="Body butter jar on patterned box"></div>
    <div class="card-name">Product Name</div>
    <div class="card-price"><span class="old">$659.00</span><span class="now">$599.99</span></div>
    <div class="card-actions"><div><svg width="18" height="18"><use href="#i-cart"/></svg></div><div><svg width="16" height="16"><use href="#i-heart"/></svg></div><div><svg width="16" height="16"><use href="#i-swap"/></svg></div><div><svg width="16" height="16"><use href="#i-go"/></svg></div></div>
  </article>
</section>

<section>
  <div class="abs news" role="img" aria-label="Orange-tinted photo of a market stall with aloe plants"></div>
  <h2 class="abs news-title">LATEST NEWS</h2>
  <div class="abs news-photo a" style="left:91px;top:1741px" role="img" aria-label="Stallholder with products and plants at an expo"></div>
  <div class="abs news-text" style="left:267px;top:1750px">
    <h3>Nemo Enim Ipsam Volup</h3>
    <div class="date">09-07-2016</div>
    <p>Lorem Ipsum has been the industry's standard dummy text ever since the 1500s, when an unknown printer took a galley of type and scrambled it to make a type specimen book.</p>
    <div class="more">Read More &gt;&gt;</div>
  </div>
  <div class="abs news-photo b" style="left:630px;top:1741px" role="img" aria-label="Outdoor market marquee with product display"></div>
  <div class="abs news-text" style="left:806px;top:1744px">
    <h3>Nemo Enim Ipsam Volup</h3>
    <div class="date">09-07-2016</div>
    <p>Lorem Ipsum has been the industry's standard dummy text ever since the 1500s, when an unknown printer took a galley of type and scrambled it to make a type specimen book.</p>
    <div class="more">Read More &gt;&gt;</div>
  </div>
</section>

<footer>
  <h4 class="abs foot-h" style="left:93px">CONTACT US</h4>
  <p class="abs foot-body" style="left:93px;top:2025px;width:260px">Address : ABN 12 345 678 901 ,Unit 7/14 Wattle Road, Greenvale NSW 2150<br>Phone : 02 9000 4120<br>Email : &nbsp;sales@larkspurcosmetics.com.au</p>

  <h4 class="abs foot-h" style="left:419px">NAVIGATE</h4>
  <ul class="abs foot-nav" style="left:419px;top:2024px">
    <li>ABOUT US</li><li>PRODUCTS</li><li>SUPPORT</li><li>NEWS</li><li>CONTACTS</li>
  </ul>

  <h4 class="abs foot-h" style="left:631px">JOIN OUR MAILING LIST</h4>
  <p class="abs foot-body" style="left:631px;top:2024px;width:220px;line-height:18px">Your about us information would fit here nicely.</p>
  <div class="abs mail-form"><div class="field">Email address</div><div class="submit">Submit</div></div>

  <h4 class="abs foot-h" style="left:936px">FOLLOW US OUT THERE</h4>
  <div class="abs social"><div></div><div></div><div></div><div></div></div>

  <div class="abs foot-rule"></div>
  <div class="abs pay">
    <div style="background:#dfe6f2"></div><div style="background:#2a4f8f"></div><div style="background:#1f3f95"></div><div style="background:#eeeeee"></div><div style="background:#3a7fc8"></div>
  </div>
  <p class="abs copyright">Copyright © 2016. All Rights Reserved</p>
</footer>
</body>
</html>
```